Flyer informing about the activities of people in action

Leute im Wandel (www.leuteimwandel.ch) offers coaching, medation, support for traumatized people and conflict and crisis intervention. The flyer should inform about the activities in a plain and simple way (see logo on the homepage).

Target Market(s)

Adults who live in Switzerland or Germany

Requirements
Must have
• - simple flyer, the design is based on my logo. Brief information about my offer, reference to my homepage www.leuteimwandel.
- 2-sided: on the first page - fire circle with text (see homepage - Home), on the back - offer with logo
- possibly a square flyer

Should not have
• no photos

```html
<!DOCTYPE html>
<html lang="de">
<head>
<meta charset="utf-8">
<title>Leute im Wandel – Angebot</title>
<link rel="stylesheet" href="https://fonts.googleapis.com/css2?family=Great+Vibes&family=Montserrat:wght@400;500&display=swap">
<style>
  :root {
    --ochre: #9b7a2f;
    --ink-light: #ffffff;
    --marker-gold: #e8b62c;
  }
  * { margin: 0; padding: 0; box-sizing: border-box; }
  html, body {
    width: 1200px;
    height: 1200px;
    overflow: hidden;
  }
  body {
    background: var(--ochre);
    color: var(--ink-light);
    font-family: "Montserrat", Arial, sans-serif;
  }
  .flyer {
    position: relative;
    width: 1200px;
    height: 1200px;
    background: var(--ochre);
  }
  .headline {
    position: absolute;
    top: 152px;
    left: 0;
    width: 100%;
    text-align: center;
    font-family: "Great Vibes", cursive;
    font-weight: 400;
    font-size: 94px;
    line-height: 1;
    white-space: nowrap;
  }
  .subline {
    position: absolute;
    top: 318px;
    left: 0;
    width: 100%;
    text-align: center;
    font-size: 33px;
    font-weight: 400;
    letter-spacing: 4.5px;
    text-transform: uppercase;
    white-space: nowrap;
  }
  .offers {
    position: absolute;
    top: 447px;
    left: 118px;
    width: 980px;
    list-style: none;
  }
  .offer {
    position: relative;
    padding-left: 79px;
    margin-bottom: 36px;
  }
  .offer-marker {
    position: absolute;
    left: 0;
    top: -1px;
    width: 44px;
    height: 44px;
  }
  .offer-title {
    font-size: 36px;
    font-weight: 500;
    letter-spacing: 2.5px;
    text-transform: uppercase;
    line-height: 40px;
    margin-bottom: 6px;
  }
  .offer-text {
    font-size: 33px;
    font-weight: 400;
    line-height: 43px;
    max-width: 900px;
  }
  .brand {
    position: absolute;
    left: 760px;
    top: 1015px;
    width: 400px;
    text-align: center;
  }
  .brand-name {
    font-size: 40px;
    font-weight: 400;
    line-height: 1.1;
    letter-spacing: 1px;
    white-space: nowrap;
  }
</style>
</head>
<body>
  <main class="flyer">
    <h1 class="headline">Ich begleite Sie und bringe Ihnen</h1>
    <p class="subline">Orientierung, Klarheit &amp; Unterstützung</p>

    <ul class="offers">
      <li class="offer">
        <svg class="offer-marker" viewBox="0 0 44 44" aria-hidden="true">
          <circle cx="22" cy="22" r="17" fill="none" stroke="var(--marker-gold)" stroke-width="4"/>
        </svg>
        <h2 class="offer-title">Coaching</h2>
        <p class="offer-text">Manchmal brauchen Sie ein Gegenüber zum Klären Ihrer Situation.</p>
      </li>
      <li class="offer">
        <svg class="offer-marker" viewBox="0 0 44 44" aria-hidden="true">
          <circle cx="22" cy="22" r="17" fill="none" stroke="var(--marker-gold)" stroke-width="4"/>
        </svg>
        <h2 class="offer-title">Begleitung</h2>
        <p class="offer-text">Manchmal brauchen Sie jemanden, bei dem Sie sich sicher fühlen.</p>
      </li>
      <li class="offer">
        <svg class="offer-marker" viewBox="0 0 44 44" aria-hidden="true">
          <circle cx="22" cy="22" r="17" fill="none" stroke="var(--marker-gold)" stroke-width="4"/>
        </svg>
        <h2 class="offer-title">Mediation</h2>
        <p class="offer-text">Manchmal brauchen Sie eine Brückenbauerin für neue Begegnungen.</p>
      </li>
    </ul>

    <div class="brand">
      <p class="brand-name">Leute im Wandel</p>
    </div>
  </main>
</body>
</html>
```